Revamp business card for upcoming new practice

We need a business card with our new practice location details. We are a boutique dental practice. Our new practice design is timeless black, white and grey colour scheme with a pop of our purple.
We are moving away from the amount of purple on website and overall practice.
Simple, elegant, clean and eye catching.

Industry/Entity Type

Dental Clinic

Contact Information for Business Card

See Design brief attached

Font styles to use
Serif
Sans Serif

Requirements
Must have
• New design | Front requirements:
• • Business logo (see attached files)
• • Address: 214 Carrow Lane Brindlewood Tas 7391
• • Phone number: 03 7346 1984
• • Email: info@norbelldental.example
• • Website address: norbelldental.example
• New design | Back requirements:
• • Dentist Details: Dr. Owen Trask & Associates
• B.D.S Ferndale Institute Leeds
• Grad. Dip. Clin. Dent. (Conscious Sedation & Pain Control). Corvale University.
• • Your Next Appointment is: OR no text and just lines for writing an appointment
• • Lines for writing the appointment minimum 2, maximum 3.
• • Cancellation Policy: We require a minimum of 48 hours or a fee will apply
Nice to have
• Black, grey and white colours with the touch of purple
Should not have
• Icon/images for contact details
• Be entirely purple.

```html
<!DOCTYPE html>
<html lang="en">
<head>
<meta charset="utf-8">
<title>Norbell Dental – Business Card</title>
<link rel="stylesheet" href="https://fonts.googleapis.com/css2?family=Ubuntu:wght@300;400;500;700&display=swap">
<style>
  :root {
    --canvas: #141414;
    --card-dark: #2b2b2b;
    --card-frame: #3a3a3a;
    --paper: #ffffff;
    --ink: #555555;
    --ink-dark: #444444;
    --light: #f2f2f2;
    --muted: #c9c9c9;
    --bar: #cfcfcf;
    --rule: #9a9a9a;
    --highlight: #5e5e5e;
    --ghost: #ececec;
  }
  * { margin: 0; padding: 0; box-sizing: border-box; }
  html, body { width: 1200px; height: 1000px; overflow: hidden; }
  body {
    background: var(--canvas);
    font-family: "Ubuntu", sans-serif;
    position: relative;
  }
  .card {
    position: absolute;
    top: 345px;
    width: 500px;
    height: 310px;
    overflow: hidden;
  }

  /* Front */
  .card-front { left: 70px; background: var(--card-dark); color: var(--light); }
  .front-address {
    position: absolute; top: 30px; left: 150px;
    font-size: 12px; font-weight: 300; color: var(--muted); letter-spacing: .2px;
  }
  .front-bar {
    position: absolute; top: 92px; right: 0;
    width: 135px; height: 20px; background: var(--bar);
  }
  .brand-name {
    position: absolute; top: 128px; left: 56px;
    font-size: 52px; font-weight: 400; color: var(--light); letter-spacing: -1px;
    display: flex; align-items: center; gap: 12px;
    white-space: nowrap;
  }
  .brand-mark { width: 12px; height: 12px; background: var(--light); }
  .front-contacts {
    position: absolute; bottom: 28px; left: 30px;
    display: flex; font-size: 12px; font-weight: 300; color: var(--muted);
  }
  .front-contacts span { padding: 0 10px; border-left: 1px solid var(--muted); }
  .front-contacts span:first-child { padding-left: 0; border-left: none; }

  /* Back */
  .card-back { left: 630px; background: var(--card-frame); padding: 18px 16px; }
  .back-panel {
    position: relative; width: 100%; height: 100%;
    background: var(--paper); color: var(--ink); overflow: hidden;
  }
  .ghost-name {
    position: absolute; top: 118px; left: 40px;
    font-size: 56px; font-weight: 400; color: var(--ghost); letter-spacing: -1px;
    white-space: nowrap;
  }
  .dentist {
    position: absolute; top: 20px; left: 0; right: 0; text-align: center;
    font-size: 22px; font-weight: 500; color: var(--ink-dark);
  }
  .dentist-name { background: var(--highlight); color: var(--paper); padding: 0 6px; }
  .credentials {
    position: absolute; top: 56px; left: 0; right: 0; text-align: center;
    font-size: 12.5px; line-height: 1.35; color: var(--ink);
  }
  .appointment-lines { position: absolute; top: 140px; left: 26px; right: 26px; }
  .appointment-lines .line { height: 1px; background: var(--rule); margin-bottom: 30px; }
  .policy {
    position: absolute; bottom: 18px; left: 0; right: 0; text-align: center;
    font-size: 11px; color: var(--ink);
  }
  .policy strong { font-weight: 700; }
</style>
</head>
<body>
  <section class="card card-front" aria-label="Business card front">
    <p class="front-address">214 Carrow Lane Brindlewood Tas 7391</p>
    <div class="front-bar"></div>
    <h1 class="brand-name"><span class="brand-mark"></span>Norbell Dental</h1>
    <p class="front-contacts">
      <span>03 7346 1984</span>
      <span>info@norbelldental.example</span>
      <span>norbelldental.example</span>
    </p>
  </section>

  <section class="card card-back" aria-label="Business card back">
    <div class="back-panel">
      <p class="ghost-name" aria-hidden="true">Norbell Dental</p>
      <h2 class="dentist"><span class="dentist-name">Dr. Owen Trask</span> &amp; Associates</h2>
      <p class="credentials">
        B.D.S Ferndale Institute Leeds<br>
        Grad. Dip. Clin. Dent. (Conscious Sedation &amp; Pain Control)<br>
        Corvale University
      </p>
      <div class="appointment-lines">
        <div class="line"></div>
        <div class="line"></div>
        <div class="line"></div>
      </div>
      <p class="policy"><strong>**Cancellation Policy:</strong> We require a minimum of 48 hours or a fee will apply</p>
    </div>
  </section>
</body>
</html>
```